IT Company that provides secure IT solutions and services to our customers

We need business cards and a logo for a new IT Solutions company just created based in Kuala Lumpur, Malaysia. But will also be serving other countries in the region. We provide secure data, voice solutions on mobile platforms. Our first offering is encrypted voice and data solutions for IOS, Android, Windows and BlackBerry devices.

Target Market(s)

large organizations Govt, Police, Defence, Anti-corruption, Legal, highly regulated industries such as Health-care, Financial, Banking, Insurance,

Industry/Entity Type

Information Technology

Contact Information for Business Card

VelmoraNet (Logo - colour is ORVEX blue)Roshan Adeel Managing Director Kryption IT Sdn. Bhd.5th Floor, Block D, Wisma PLB,No.14 Jalan Seri Melor,50470, Kuala LumpurMalaysia

Font styles to use
Sans Serif

Colors
3176b5
ec1f27
fbed22

Requirements
Must have
• VelmoraNet all in Blue like ORVEX blue. A logo design perhaps a play of VN, K with a dangling T (colour can be any)
Nice to have
• I want a clean crisp card, not too busy, easy to read.

```html
<!DOCTYPE html>
<html lang="en">
<head>
<meta charset="utf-8">
<title>VelmoraNet Business Card</title>
<link rel="stylesheet" href="https://fonts.googleapis.com/css2?family=Montserrat:wght@500&family=Source+Sans+3:wght@400;700&display=swap">
<style>
  :root {
    --backdrop: #111111;
    --paper: #ffffff;
    --brand-blue: #1f5ba8;
    --ink-blue: #1c55a6;
    --ink-grey: #3a3a3a;
    --mark-grey: #4a4a4a;
    --emboss-dark: #163f78;
    --emboss-light: #6f8fd6;
  }
  * { margin: 0; padding: 0; box-sizing: border-box; }
  html, body { width: 1200px; height: 900px; overflow: hidden; background: var(--backdrop); }
  .canvas { position: relative; width: 1200px; height: 900px; }
  .card { position: absolute; top: 170px; width: 347px; height: 561px; }
  .card-front { left: 259px; background: var(--paper); }
  .card-back { left: 631px; background: var(--brand-blue); }
  .accent-band { position: absolute; left: 102px; width: 143px; height: 29px; background: var(--brand-blue); }
  .accent-band.top { top: 0; }
  .accent-band.bottom { bottom: 0; }
  .brand-dot { position: absolute; left: 141px; top: 119px; width: 64px; height: 64px; border: 3px solid var(--mark-grey); border-radius: 50%; }
  .brand-name { position: absolute; top: 190px; width: 100%; text-align: center; font-family: "Montserrat", sans-serif; font-weight: 500; font-size: 46px; color: var(--ink-blue); letter-spacing: -0.5px; }
  .contact { position: absolute; top: 284px; width: 100%; text-align: center; font-family: "Source Sans 3", sans-serif; color: var(--ink-grey); font-size: 15.5px; line-height: 20px; }
  .person-name, .company-name { font-weight: 700; color: var(--ink-blue); font-size: 18px; }
  .role { margin-bottom: 18px; }
  .back-circle { position: absolute; left: 34px; top: 145px; }
</style>
</head>
<body>
<main class="canvas">
  <section class="card card-front">
    <div class="accent-band top"></div>
    <div class="brand-dot"></div>
    <h1 class="brand-name">VelmoraNet</h1>
    <address class="contact" style="font-style: normal;">
      <div class="person-name">Roshan Adeel</div>
      <div class="role">Managing Director</div>
      <div class="company-name">Velmora Net</div>
      <div>Sdn. Bhd. 5th Floor, Block D,</div>
      <div>Wisma PLB,No.14 Jalan Seri Melor,</div>
      <div>50470, Kuala Lumpur</div>
      <div>Malaysia</div>
    </address>
    <div class="accent-band bottom"></div>
  </section>
  <section class="card card-back">
    <svg class="back-circle" width="280" height="280" viewBox="0 0 280 280" aria-hidden="true">
      <circle cx="140" cy="141" r="136" fill="none" stroke="var(--emboss-light)" stroke-width="2"/>
      <circle cx="140" cy="139" r="136" fill="none" stroke="var(--emboss-dark)" stroke-width="2"/>
    </svg>
  </section>
</main>
</body>
</html>
```